Brambleton Pizza Website

We are working with Brambleton Pizza and designing them a website.

Some sites to use for content/competitors and inspiration:

https://fennimores.com
https://www.bhq-eats.com
https://brightorchard.com/en-us/

Thank you for taking the time to consider designing a website for us. We are web developers based in Stockton, CA, USA. Most of our projects go through the same process. Understanding this process may help you win a project with us. We custom-code all of our websites in-house. We don’t have any requirements as to what tools you use for your design, but we prefer Figma files. For any design that we label as four-stars, we send it to the client for review. The client picks the final design they want us to use. Once we complete this process, we will continue to show additional clients all the four-star sites and purchase them later. Your designs will have multiple chances to sell. For better chances of success, we ask that you follow these guidelines.

IMAGES:
If you use any images or icons in the design, we ask that you have a link to the asset so we can purchase the image/icon. Most of the designs we submit do not have the customer’s images on them unless they have some great images. Be creative; show us the feeling you are trying to portray with your image choices. Use any royalty-free site you choose. We subscribe to Quillstone and mainly use their images, but we can purchase images outside of Quillstone.

PLEASE NOTE: we will not submit designs to clients with watermarks on the images.

FONTS:
We ask that you identify the fonts used in the design. This can be done in a message if you want. We typically use Google Fonts and Quillstone Fonts.

CONTENT:
We're always open to different content and ideas. We often submit designs with stock images so the client can see our vision. We typically take pictures after the website launch to use their images with our vision. Lorem Ipsum is fine for paragraphs, but we ask that you write the headers in correct English. We want to be able to show the vision and identify the sections of the website.

INSPIRATION:
We typically add a couple of links in the brief of websites we like to help you get started in your design.

REVISIONS:
We do not often ask for revisions of the designs unless we see something in the design that may not appeal to the client. If there are slight changes that we want to make, we do that in the development process.

FEEDBACK:
We rarely give feedback on designs during the design process. We are working on many website projects and do not have the time to provide feedback. We usually respond if your request is well thought out and asks specific questions, but a note asking “feedback, please” usually goes unanswered.

```html
<!DOCTYPE html>
<html lang="en">
<head>
<meta charset="utf-8">
<title>Brambleton Pizza</title>
<link href="https://fonts.googleapis.com/css2?family=Barlow+Condensed:ital,wght@1,400;1,500;1,600&family=Poppins:wght@400;500;600&display=swap" rel="stylesheet">
<style>
:root{
  --green:#3bb24a;
  --red:#e3272b;
  --red-band:#e52a2c;
  --dark:#120d0a;
  --ink:#2b2b2b;
  --white:#ffffff;
  --marble:#ececec;
  --footer:#050505;
}
*{margin:0;padding:0;box-sizing:border-box}
html,body{width:1200px;height:4361px;overflow:hidden;background:var(--white)}
body{position:relative;font-family:"Poppins",sans-serif;color:var(--ink)}
.abs{position:absolute}
.display{font-family:"Barlow Condensed",sans-serif;font-style:italic;font-weight:500;text-transform:uppercase;letter-spacing:.5px}
.btn{position:absolute;display:flex;align-items:center;justify-content:center;font-size:13px;font-weight:500;border-radius:4px;text-transform:uppercase}
.btn-green{background:var(--green);color:var(--white)}
.photo{position:absolute;border-radius:8px}

/* hero */
.hero{position:absolute;left:0;top:0;width:1200px;height:855px;background:radial-gradient(ellipse at 75% 45%,#6b3a1e 0%,#3a2314 40%,#1a110b 80%);overflow:hidden}
.hero-photo{position:absolute;left:180px;top:200px;width:1020px;height:640px;background:radial-gradient(ellipse at 55% 65%,#d9803a 0%,#b8532a 35%,#5a3422 65%,transparent 80%)}
.hero-slice{position:absolute;left:640px;top:230px;width:400px;height:420px;border-radius:50%;background:radial-gradient(circle,#f1e3b8 0%,#e6c27c 45%,transparent 72%)}
.brand{position:absolute;left:92px;top:30px;display:flex;align-items:center;gap:8px;color:var(--white);font-family:"Poppins",sans-serif;font-weight:600;font-size:13px;line-height:1.1}
.brand .mark{width:14px;height:14px;border-radius:50%;background:var(--white)}
.nav{position:absolute;top:36px;color:var(--white);font-size:13.5px;font-weight:600}
.hero h1{position:absolute;left:90px;top:150px;color:var(--white);font-size:76px;line-height:86px;font-weight:400}
.hero .lead{position:absolute;left:90px;top:329px;width:420px;color:var(--white);font-size:13.5px;line-height:19px}
.btn-outline{border:1.5px solid var(--white);color:var(--white)}
.search{position:absolute;left:90px;top:465px;width:428px;height:45px;background:var(--white);border-radius:4px;display:flex;align-items:center;padding-left:20px;font-size:10.5px;color:#888;gap:14px}
.search .go{position:absolute;right:0;top:0;width:107px;height:45px;background:var(--green);color:var(--white);display:flex;align-items:center;justify-content:center;border-radius:0 4px 4px 0;font-size:14px}

/* about */
.section-title{position:absolute;color:var(--red);font-size:38px}
.bar{position:absolute;width:2px;background:var(--red)}
.copy{position:absolute;width:372px;font-size:13.5px;line-height:19.5px;color:#333}
.frame{position:absolute;border:2px solid var(--red);border-radius:0 0 8px 8px;border-top-left-radius:0}

/* offerings */
.offerings{position:absolute;left:0;top:1779px;width:1200px;height:656px;background:linear-gradient(135deg,#f1f1f1,#e4e4e4 50%,#efefef)}
.card{position:absolute;top:1960px;width:268px;height:343px;border-radius:8px;overflow:hidden}
.card span{position:absolute;left:0;right:0;bottom:30px;text-align:center;color:var(--white);font-size:36px}

/* best */
.best{position:absolute;left:0;top:2436px;width:1200px;height:521px;background:linear-gradient(90deg,#2a2522 0%,#1d1b1a 60%,#141312 100%)}
.best-box{position:absolute;left:691px;top:2574px;width:357px;height:259px;background:rgba(120,120,120,.55);border-radius:6px;text-align:center;padding-top:60px}
.best-box h2{color:var(--red);font-size:36px}
.best-box p{margin:8px auto 0;width:300px;color:var(--white);font-size:13px;line-height:19px}

/* updates */
.updates{position:absolute;left:0;top:3600px;width:1200px;height:362px;background:var(--red-band)}
.updates h2{position:absolute;left:147px;top:3752px;color:var(--white);font-size:38px;line-height:41px;font-weight:400}
.updates-copy{position:absolute;left:147px;top:3842px;width:470px;color:var(--white);font-size:13px;line-height:18px}
.btn-white{background:var(--white);color:var(--red);font-weight:600;border-radius:6px}

/* footer */
.footer{position:absolute;left:0;top:3960px;width:1200px;height:401px;background:var(--footer);color:var(--white)}
.footer h3{position:absolute;top:4080px;font-size:26px;color:var(--white)}
.links{position:absolute;left:345px;top:4128px;font-size:13.5px;line-height:17.5px;color:var(--white);list-style:none}
.contact-row{position:absolute;left:555px;display:flex;align-items:center;gap:9px;font-size:13.5px;color:var(--white)}
.newsletter{position:absolute;left:841px;top:4131px;width:271px;height:43px;background:var(--white);border-radius:3px;display:flex;align-items:center;padding-left:20px;font-size:13px;color:#555}
.legal{position:absolute;left:130px;top:4326px;font-size:12.5px;color:var(--white)}
.social{position:absolute;top:4320px;width:26px;height:26px;border-radius:50%;background:var(--red)}
</style>
</head>
<body>

<!-- HERO -->
<section class="hero">
  <div class="hero-photo" role="img" aria-label="Cheesy pizza slice being lifted from a pizza on a wooden board"></div>
  <div class="hero-slice" role="img" aria-label="Melted cheese stretching from the slice"></div>
  <div class="brand"><span class="mark"></span><span>BRAMBLETON<br>PIZZA</span></div>
  <span class="nav" style="left:247px">HOME</span>
  <span class="nav" style="left:323px">MENU</span>
  <span class="nav" style="left:398px">LOCATIONS</span>
  <span class="nav" style="left:514px">GATERINDS &amp; EVENTS</span>
  <span class="nav" style="left:697px">GIFT CARSD ABOUT</span>
  <svg class="abs" style="left:898px;top:38px" width="14" height="14" viewBox="0 0 14 14"><path d="M2 5h10l-1 8H3z M5 5V3a2 2 0 0 1 4 0v2" fill="none" stroke="#3bb24a" stroke-width="1.5"/></svg>
  <svg class="abs" style="left:927px;top:38px" width="14" height="14" viewBox="0 0 14 14"><circle cx="6" cy="6" r="4" fill="none" stroke="#3bb24a" stroke-width="1.6"/><path d="M9 9l3.5 3.5" stroke="#3bb24a" stroke-width="1.6"/></svg>
  <a class="btn btn-green" style="left:966px;top:22px;width:146px;height:46px;font-weight:600">Contact</a>
  <h1 class="display">Home of the original<br>chicken pizza</h1>
  <p class="lead">Reference site about Lorem Ipsum, giving information on its origins, as well as a random Lipsum generator.</p>
  <a class="btn btn-green" style="left:90px;top:391px;width:233px;height:46px">Download Full Menu</a>
  <a class="btn btn-outline" style="left:332px;top:391px;width:186px;height:46px">Request a Quote</a>
  <div class="search">
    <svg width="11" height="11" viewBox="0 0 14 14"><circle cx="6" cy="6" r="4" fill="none" stroke="#777" stroke-width="1.6"/><path d="M9 9l3.5 3.5" stroke="#777" stroke-width="1.6"/></svg>
    <span>Search for Menu Item</span>
    <span class="go">SEARCH</span>
  </div>
  <svg class="abs" style="left:0;top:760px" width="1200" height="95" viewBox="0 0 1200 95" preserveAspectRatio="none"><path d="M0 70 L40 55 L70 75 L110 60 L150 78 L200 62 L240 80 L300 66 L340 82 L400 68 L460 84 L520 70 L560 86 L620 72 L680 88 L740 70 L800 84 L860 68 L920 80 L980 60 L1040 74 L1090 50 L1140 68 L1200 40 L1200 95 L0 95 Z" fill="#fff"/></svg>
</section>

<!-- ABOUT -->
<div class="abs" role="img" aria-label="Whole pizza seen from above" style="left:-42px;top:910px;width:300px;height:300px;border-radius:50%;background:radial-gradient(circle,#e59b4a 0%,#c9672c 55%,#e3b56a 70%,#d08a3c 100%)"></div>
<div class="abs" role="img" aria-label="Tomatoes with basil leaves" style="left:210px;top:900px;width:110px;height:80px;border-radius:50%;background:radial-gradient(circle at 35% 55%,#d8251f 0 22%,#3f7a2a 40%,transparent 70%)"></div>
<div class="abs" role="img" aria-label="Basil leaf" style="left:0;top:1220px;width:60px;height:80px;border-radius:50%;background:radial-gradient(circle,#3f7a2a 0,transparent 70%)"></div>
<div class="abs" role="img" aria-label="Silver fork and spoon" style="left:1040px;top:1190px;width:160px;height:220px;border-radius:40%;background:radial-gradient(ellipse,#d8d8d8 0,#b5b5b5 35%,transparent 70%)"></div>

<div class="bar" style="left:323px;top:982px;height:44px"></div>
<h2 class="section-title display" style="left:343px;top:980px">Architecture</h2>
<p class="copy" style="left:323px;top:1043px">Morbi accumsan ipsum velit. Nam nec tellus a odio tincidunt auctor a ornare odio. Sed non mauris vitae erat consequat auctor eu in elit. Class aptent taciti sociosqu ad litora torquent per conubia nostra, per inceptos himenaeos. Mauris in erat justo.</p>
<h2 class="section-title display" style="left:734px;top:980px">Hand-picked tomatoes</h2>
<p class="copy" style="left:734px;top:1043px">Nullam ac urna eu felis dapibus condimentum sit amet a augue. Sed non neque elit. Sed ut imperdiet nisi. Proin condimentum fermentum nunc. Etiam pharetra, erat sed fermentum feugiat, velit mauris egestas quam, ut aliquam massa nisl quis neque.</p>
<a class="btn btn-green" style="left:734px;top:1173px;width:146px;height:46px;font-weight:600">Read More</a>

<div class="frame" style="left:692px;top:1318px;width:342px;height:324px"></div>
<div class="photo" role="img" aria-label="Pizza with olives and peppers on a dark wooden table" style="left:183px;top:1225px;width:477px;height:327px;background:radial-gradient(circle at 55% 50%,#e0a152 0 30%,#3a3634 48%,#1c1b1b 100%)"></div>
<div class="photo" role="img" aria-label="Sliced pepperoni and mushroom pizza on a wooden board" style="left:604px;top:1346px;width:412px;height:274px;background:radial-gradient(circle at 60% 50%,#c9623a 0 32%,#7a5a44 55%,#4b3a2e 100%)"></div>

<!-- OFFERINGS -->
<section class="offerings"></section>
<div class="abs" role="img" aria-label="Cherry tomatoes on a vine with parsley" style="left:0;top:1715px;width:220px;height:180px;border-radius:50%;background:radial-gradient(circle at 20% 70%,#d8251f 0 10%,#3f7a2a 30%,transparent 65%)"></div>
<div class="bar" style="left:256px;top:1879px;height:44px"></div>
<h2 class="section-title display" style="left:276px;top:1877px">Our delicious offeringe</h2>
<div class="card" style="left:181px" role="img" aria-label="Fresh green salad in a bowl on dark wood"><div class="abs" style="inset:0;background:linear-gradient(180deg,#3d6a2c 0%,#2f3a22 45%,#2a1f17 100%)"></div><span class="display">Salad</span></div>
<div class="card" style="left:465px" role="img" aria-label="Berry mousse desserts on a cooling rack"><div class="abs" style="inset:0;background:linear-gradient(180deg,#1d1d1f 0%,#7a2a2a 40%,#242426 70%,#121214 100%)"></div><span class="display">Desserts</span></div>
<div class="card" style="left:751px" role="img" aria-label="Penne pasta with tomato in a bowl"><div class="abs" style="inset:0;background:radial-gradient(circle at 50% 32%,#d9a04a 0 25%,#8a3a2a 35%,#3a3a3a 55%,#1e1e1e 100%)"></div><span class="display">Pastas</span></div>

<!-- WE MAKE THE BEST -->
<section class="best"></section>
<div class="abs" role="img" aria-label="Pizza on a dark slate with tomatoes, mushrooms and onion rings" style="left:0;top:2436px;width:677px;height:521px;background:radial-gradient(circle at 45% 48%,#e38a3e 0 24%,#3a3330 40%,transparent 72%)"></div>
<div class="best-box">
  <h2 class="display">We make the best</h2>
  <p>We provide you with complete meal prep which includes the prepackaged necessary ingredients for a Pizza Feast as well as an easy to follow recipe.</p>
</div>

<!-- GALLERY -->
<div class="photo" role="img" aria-label="Hands taking slices of pizza" style="left:183px;top:3065px;width:269px;height:193px;background:radial-gradient(circle,#e0904a 0 35%,#2c3a38 70%)"></div>
<div class="photo" role="img" aria-label="Close-up of pizza slice with melting cheese" style="left:465px;top:3065px;width:270px;height:193px;background:linear-gradient(135deg,#e6a24e,#d0553a 50%,#eac07a)"></div>
<div class="photo" role="img" aria-label="Margherita pizza on a dark table" style="left:750px;top:3065px;width:269px;height:193px;background:radial-gradient(circle,#e4a252 0 33%,#2b3234 65%)"></div>
<div class="photo" role="img" aria-label="Pepperoni pizza" style="left:181px;top:3278px;width:269px;height:193px;background:radial-gradient(circle,#b8432a 0 35%,#d89a4a 45%,#3a2c22 70%)"></div>
<div class="photo" role="img" aria-label="Vegetable pizza with a slice removed" style="left:464px;top:3278px;width:269px;height:193px;background:radial-gradient(circle,#cf6a34 0 35%,#5a4a3c 70%)"></div>
<div class="photo" role="img" aria-label="Heart-shaped pizza on baking paper" style="left:748px;top:3278px;width:268px;height:193px;background:radial-gradient(circle,#c9503a 0 30%,#9a7050 50%,#2c2624 75%)"></div>

<!-- UPDATES -->
<svg class="abs" style="left:0;top:3520px" width="1200" height="90" viewBox="0 0 1200 90" preserveAspectRatio="none"><path d="M0 30 L50 18 L90 40 L140 24 L200 46 L260 30 L320 50 L380 36 L440 56 L500 40 L560 62 L620 44 L680 66 L720 54 L780 70 L840 50 L900 60 L960 40 L1020 52 L1080 30 L1140 44 L1200 28 L1200 90 L0 90 Z" fill="#e52a2c"/></svg>
<section class="updates"></section>
<div class="abs" role="img" aria-label="Sliced pepperoni pizza" style="left:978px;top:3368px;width:300px;height:308px;border-radius:50%;background:radial-gradient(circle,#d96a34 0 45%,#e2a255 60%,#c57a34 70%)"></div>
<h2 class="updates display" style="all:unset"></h2>
<h2 class="display" style="position:absolute;left:147px;top:3752px;color:#fff;font-size:38px;line-height:41px;font-weight:400">Get updates about new dishes<br>and upcoming events</h2>
<p class="updates-copy">Quisque maximus libero leo, pellentesque sagittis nisi rutrum a. Ut sed placerat dui. Sed fermentum velit sed nibh condimentum egestas.</p>
<a class="btn btn-white" style="left:909px;top:3796px;width:145px;height:48px">Subcribe Now</a>

<!-- FOOTER -->
<footer class="footer"></footer>
<div class="abs" style="left:85px;top:4150px;display:flex;align-items:center;gap:10px;color:#fff;font-size:22px;font-weight:600;line-height:1.1">
  <span style="width:16px;height:16px;border-radius:50%;background:#fff"></span><span>BRAMBLETON<br>PIZZA</span>
</div>
<h3 class="display" style="left:344px">Quick links</h3>
<ul class="links"><li>Home</li><li>Menu</li><li>Locations</li><li>Gaterinds &amp; Events</li><li>Gift Carsd About</li><li>contact</li></ul>
<h3 class="display" style="left:555px">Contact</h3>
<div class="contact-row" style="top:4127px"><svg width="11" height="11" viewBox="0 0 12 12"><path d="M2 1l3 1 0 3-1 1a7 7 0 0 0 3 3l1-1 3 0 1 3c-6 1-11-4-10-10z" fill="#fff"/></svg>(123) 456-789</div>
<div class="contact-row" style="top:4164px"><svg width="11" height="12" viewBox="0 0 12 14"><path d="M6 0a5 5 0 0 1 5 5c0 4-5 9-5 9S1 9 1 5a5 5 0 0 1 5-5z" fill="#fff"/><circle cx="6" cy="5" r="2" fill="#050505"/></svg>Info Brambleton</div>
<div class="contact-row" style="top:4199px"><svg width="12" height="10" viewBox="0 0 12 10"><rect width="12" height="10" fill="#fff"/><path d="M0 0l6 5 6-5" fill="none" stroke="#050505" stroke-width="1.2"/></svg>info@brambletonpizza.com</div>
<h3 class="display" style="left:841px">Newsletter</h3>
<div class="newsletter">Ente Your Email
  <svg class="abs" style="left:228px;top:14px" width="14" height="14" viewBox="0 0 14 14"><path d="M1 7l12-6-4 12-2-5z" fill="#e3272b"/></svg>
</div>
<div class="abs" style="left:130px;top:4304px;width:938px;height:1px;background:#555"></div>
<p class="legal">PRIVACY POLICY | DISCLAIMER</p>
<span class="social" style="left:940px"></span>
<span class="social" style="left:974px"></span>
<span class="social" style="left:1008px"></span>
<span class="social" style="left:1043px"></span>
<span class="abs" style="left:1132px;top:4298px;width:38px;height:38px;border-radius:50%;background:var(--red)"></span>

</body>
</html>
```